Dietary supplement, Clean and simple.

Hi,
I’d like to talk about the project,

About us:
We are a dietary supplement (Vitamins, Minerals, amino acids etc.) company.
The goal is to have about 25 products at the end of this year. However, for this goal to be achieved we need a good label design to make our products represent our company values.
I’ll be here every day supporting your questions, we are fully committed to making the highest/best quality/customer experience possible.

About the design and our values:
- Professional (We are in the industry of professionalism and expertise. I would love to show we are competent at this, Id. Like to have the labels looks like we have done our research.)
- Efficient (White spacing, good use of the space available.)
- Simple (Straight forward, in 5 seconds they have to know what the product they have is/how functions. We’re trying to simplify it for the consumer.
- No distractions (the only visually “distracting” factor can be the vector art.)

The guidelines:
The goal is to have a universal design, with one element that changes (Vector art). I’ll attach a file/multiple files I think can show some visuals on what I’m looking for, and what parts of the design I think are good/bad.

Label size: 69x155mm (Front is 77.5mm)

Design whatever you think fits our image. You’re the design expert, all I care about is that it fits our company standards/image.

Use this color/font.
Font: Sans Serif
Main company color is Mind green #237D62 (Use this color for something in the design.)

What I thought would be cool/might looks ugly, who knows:
1. The front of the label: Should have 1 vector art, preferably in the top right corner. (That looks good in multiple colors. The vector can have multiple areas to color, I would prefer 2 main colors in the vector art. The interchangeable colors are used for multiple kinds of products.)
2. Text/product information on the left. The text that will have to be displayed:
- Product name for instance “Magnesium + B6”
- Description for the product for instance “Magnesium with ginger taste”
- Company name or logo. (Add ® behind it. We are soon to be trademark registered.)
3. We need to show the "daily intake" amount on the front and also the amount in the complete bottle. For instance, “Daily intake 1 capsule, 60 capsules”.
• You don’t have to design the backside of the label. After I chose a design, I’d like to chat and give specific information on what areas need to be assigned where. (Too complex because of the law.)
Updates

Hi, Please make the deadline 31 days total. I want designers to have the time to design. And not be rushed to finish it.

I want to extend the deadline because i feel like a slightly more medical look would be interesting. Hope you can come up with something!!

Target Market(s)

Dietary supplement consumers

Industry/Entity Type

Dietary supplements

Font styles to use
Sans Serif

Colors

Designer to choose colors to be used in the design.

Requirements
Must have
• Trademark icon "®" has to be at the top right after the company logo(text of logo)/name.

```html
<!DOCTYPE html>
<html lang="en">
<head>
<meta charset="utf-8">
<title>MGN B+ Label</title>
<link href="https://fonts.googleapis.com/css2?family=Lexend:wght@400;600;700&display=swap" rel="stylesheet">
<style>
  :root {
    --peach-light: #FCD1A4;
    --clay: #CF9068;
    --orange: #F5A552;
    --plum: #4E1838;
    --mind-green: #237D62;
    --white: #FFFFFF;
  }
  html, body {
    margin: 0;
    padding: 0;
    overflow: hidden;
    background: var(--white);
  }
  .label {
    position: relative;
    width: 1200px;
    height: 532px;
    overflow: hidden;
    background: var(--white);
    font-family: "Lexend", sans-serif;
  }
  .label-waves {
    position: absolute;
    inset: 0;
    width: 1200px;
    height: 532px;
  }
  .brand {
    position: absolute;
    left: 690px;
    top: 68px;
    width: 180px;
    text-align: center;
    color: var(--mind-green);
    font-weight: 700;
    font-size: 27px;
    line-height: 1;
    white-space: nowrap;
  }
  .brand sup {
    font-size: 10px;
    vertical-align: top;
  }
  .product {
    position: absolute;
    left: 417px;
    top: 204px;
    width: 400px;
    text-align: center;
    color: var(--plum);
  }
  .product-name {
    margin: 0;
    font-weight: 700;
    font-size: 52px;
    line-height: 1;
    letter-spacing: 0.5px;
  }
  .product-desc {
    margin: 2px 0 0;
    font-weight: 400;
    font-size: 18px;
    line-height: 1.1;
  }
  .dose-badge {
    position: absolute;
    left: 684px;
    top: 359px;
    width: 126px;
    height: 119px;
    box-sizing: border-box;
    padding: 7px;
    border-radius: 28px;
    background: var(--peach-light);
  }
  .dose-inner {
    width: 100%;
    height: 100%;
    border-radius: 22px;
    background: var(--orange);
    color: var(--plum);
    text-align: center;
    box-sizing: border-box;
    padding-top: 5px;
  }
  .dose-daily {
    font-size: 11.5px;
    font-weight: 400;
    line-height: 1.15;
  }
  .dose-amount {
    font-size: 15px;
    font-weight: 600;
    line-height: 1.1;
  }
  .dose-rule {
    height: 2px;
    margin: 4px 2px 2px;
    background: var(--white);
  }
  .dose-count {
    font-size: 42px;
    font-weight: 700;
    line-height: 0.9;
  }
  .dose-unit {
    font-size: 10.5px;
    font-weight: 600;
    line-height: 1.1;
  }
  .weight-seal {
    position: absolute;
    left: 344px;
    top: 452px;
    width: 44px;
    height: 44px;
    border-radius: 50%;
    background: var(--white);
    color: var(--clay);
    text-align: center;
    display: flex;
    flex-direction: column;
    justify-content: center;
  }
  .weight-value {
    font-size: 15px;
    font-weight: 700;
    line-height: 1;
  }
  .weight-unit {
    font-size: 7.5px;
    font-weight: 600;
    line-height: 1;
  }
</style>
</head>
<body>
<div class="label">
  <svg class="label-waves" viewBox="0 0 1844 816" preserveAspectRatio="none" aria-hidden="true">
    <path class="top-shadow" fill="#CF9068" d="M0,0 C250,110 500,225 710,228 C900,228 1000,120 1030,0 Z"/>
    <path class="top-swoosh" fill="#FCD1A4" d="M0,0 L1030,0 C980,150 850,198 700,195 C500,190 250,100 0,0 Z"/>
    <path class="bottom-band" fill="#CF9068" d="M700,592 C850,520 1000,500 1100,505 C1300,515 1450,600 1560,640 C1680,680 1780,620 1844,555 L1844,632 C1760,660 1680,670 1580,660 C1450,640 1300,550 1100,525 C950,512 820,540 700,592 Z"/>
    <path class="bottom-field" fill="#CF9068" d="M12,578 C150,680 500,700 820,595 C950,565 1100,560 1250,600 C1450,650 1650,700 1844,688 L1844,816 L12,816 Z"/>
  </svg>

  <div class="brand">Noble Calm<sup>®</sup></div>

  <div class="product">
    <h1 class="product-name">MGN B+</h1>
    <p class="product-desc">Magnesium with lemon taste</p>
  </div>

  <div class="dose-badge">
    <div class="dose-inner">
      <div class="dose-daily">take daily</div>
      <div class="dose-amount">1 CAPSULE</div>
      <div class="dose-rule"></div>
      <div class="dose-count">60</div>
      <div class="dose-unit">CAPSULES</div>
    </div>
  </div>

  <div class="weight-seal">
    <div class="weight-value">180</div>
    <div class="weight-unit">grams</div>
  </div>
</div>
</body>
</html>
```